Pinecrest Real Estate A5 Flyer

A5 Flyer for print distribution.

Front (include attached photo and branding):
Pinecrest are a new face in the Dunmore & Kelvinhurst real estate market. The Pinecrest team are both Dunmore ‘locals’ and are genuinely and sincerely committed to this community. They put people first and pursue exceptional outcomes for their clients. This is the founding vision of Pinecrest.

Values:
Outstanding Customer Service
Timely Communication
Integrity Always
People First
Exceptional Negotiation

If you’re thinking of selling, interested in a free market appraisal, or simply want to find out more about the Pinecrest team, please reach out to Trevor or Owen for a chat. We’d love to shout you a coffee at The Marigold Coffee + Kitchen.

Pinecrest Real Estate
E: hello@pinecrestrealestate-example.com.au
W: pinecrestrealestate-example.com.au

Back (half the page about Trevor, other half the page about Owen). Please include headshots (Owen is the younger one):

Owen Pritchard (Property Consultant):

Owen has an in-depth understanding of all things property & finance related. With a degree in property & finance, diploma in finance & mortgage broking, certificate IV in real estate practice, project management roles in residential property development, plus years of small business experience as co-founder/co-owner of The Marigold Coffee + Kitchen, his experience in managing competing demands and complex scenarios runs far and wide.

Owen also has experience in corporate negotiations which is proving to be a very beneficial skill set. Owen is deeply committed to people and pursuing exceptional outcomes for his clients. He has built a reputation as a man of his word who is genuine and sincere and willing to go above and beyond for his clients.

owen@pinecrestrealestate-example.com.au
0400 118 204

Trevor Bungey (Director / Licensee):

Trevor has worked in various roles inclusive of being a Real Estate Agent, Bank Manager, Financial Counsellor, Mortgage Broker, and previously a Commercial Pilot. He spent eight years in remote Western Australia, where he worked for an international mining company creating strategies to help support the well-being of employees. Trevor’s focus in life has always been to help people. To him, it is always about the relationship. Trevor gets enormous satisfaction from seeing individuals, families, and businesses thrive financially. He has become a skilled negotiator with extensive experience working for a number of corporations and private firms.
 
What differentiates Trevor is his compassion and commitment to people. He works hard to be an excellent communicator with the aim of achieving great results. He  has extensive sales experience with incredible ability to push the boundaries, think outside the box and meet or surpass expectations. This is why his clients keep coming back and continue to refer well into the future. 

trevor@pinecrestrealestate-example.com.au
0400 362 917

Target Market(s)

House Sellers / House Buyers

Industry/Entity Type

Real Estate

Colors
0054AA
0677BA
7BADD7
CADEEF
E8F1F8

Requirements
Must have
• Branding / logo, river photo, head shots, company details etc
Nice to have
• Design as per attached branding guide

```html
<!DOCTYPE html>
<html lang="en">
<head>
<meta charset="utf-8">
<title>Pinecrest Real Estate – A5 Flyer</title>
<link rel="stylesheet" href="https://fonts.googleapis.com/css2?family=EB+Garamond:wght@400;500;700&family=Poppins:wght@300;400&display=swap">
<style>
:root{
  --navy:#1b2535;
  --panel:#dde0e5;
  --slate:#7d8699;
  --paper:#ffffff;
  --backdrop:#d3d4d6;
  --ink:#1b2535;
  --muted:#3a4354;
  --line:#c4c8cf;
}
*{box-sizing:border-box;margin:0;padding:0}
html,body{width:1200px;height:3432px;overflow:hidden}
body{background:var(--backdrop);font-family:"Poppins",sans-serif;color:var(--ink);position:relative}

.page{position:absolute;left:150px;width:900px;height:1286px;background:var(--paper);overflow:hidden;box-shadow:0 2px 6px rgba(0,0,0,.12)}
.page--front{top:380px}
.page--back{top:1746px}

/* FRONT */
.brand-header{position:absolute;left:0;top:0;width:900px;height:213px;display:flex;align-items:center;justify-content:center;gap:28px}
.brand-dot{width:80px;height:80px;border-radius:50%;background:var(--navy)}
.brand-name{font-family:"EB Garamond",serif;font-weight:500;font-size:50px;letter-spacing:17px;color:var(--navy)}
.hero-photo{position:absolute;left:0;top:213px;width:900px;height:422px;
  background:linear-gradient(180deg,#e4e9ec 0%,#cdd5d9 20%,#8a9779 40%,#5f7462 52%,#4d6d82 68%,#2f6088 100%)}
.intro{position:absolute;left:0;top:635px;width:524px;height:321px;background:var(--navy);color:#fff;padding:32px 36px 0 56px}
.intro__title{font-family:"EB Garamond",serif;font-weight:700;font-size:26px;line-height:28px;letter-spacing:.2px}
.intro__body{margin-top:10px;font-weight:300;font-size:17.5px;line-height:25px}
.intro__vision{margin-top:12px;display:inline-block;border:1.5px solid #c9ced8;border-radius:5px;padding:2px 24px;font-weight:300;font-size:17px}
.reasons{position:absolute;left:56px;top:978px;display:flex}
.reasons__item{font-size:14.5px;line-height:20px;font-weight:300;color:var(--muted);padding:0 14px}
.reasons__item:first-child{padding-left:0;width:110px}
.reasons__item:nth-child(2){width:142px;border-left:1px solid var(--line);border-right:1px solid var(--line)}
.reasons__item:nth-child(3){width:170px}
.invite{position:absolute;left:56px;top:1071px;width:406px;height:102px;background:var(--slate);border-radius:12px;color:#fff;padding:14px 24px;font-size:17.5px;line-height:25px;font-weight:300}
.invite strong{font-family:"EB Garamond",serif;font-weight:700;font-size:19.5px}
.front-contact{position:absolute;left:56px;top:1196px;width:448px;display:flex;align-items:flex-start;gap:12px}
.front-contact__name{font-family:"EB Garamond",serif;font-weight:700;font-size:19px;line-height:26px;white-space:nowrap}
.contact-lines{font-size:12.5px;line-height:26px;font-weight:300;color:var(--muted);white-space:nowrap}
.contact-lines div{display:flex;align-items:center;gap:8px}
.contact-lines svg{width:14px;height:14px;flex:none}

.values{position:absolute;left:524px;top:635px;width:376px;height:651px;background:var(--panel)}
.values__title{position:absolute;top:38px;left:0;width:376px;text-align:center;font-family:"EB Garamond",serif;font-weight:700;font-size:41px;letter-spacing:.5px}
.value{position:absolute;left:54px;display:flex;align-items:center;gap:24px}
.value__icon{width:64px;height:64px;border-radius:50%;background:var(--navy);display:flex;align-items:center;justify-content:center;flex:none}
.value__icon svg{width:34px;height:34px}
.value__label{font-family:"EB Garamond",serif;font-size:28px;line-height:28px;color:var(--navy)}

/* BACK */
.profile{position:absolute;left:0;width:900px}
.profile--owen{top:0;height:573px;background:var(--paper)}
.profile--trevor{top:573px;height:617px;background:var(--navy);color:#fff}
.bio{position:absolute;font-weight:300;text-align:justify;letter-spacing:-.2px}
.profile--owen .bio{left:52px;top:56px;width:522px;font-size:16.5px;line-height:23.5px;color:var(--muted)}
.profile--trevor .bio{left:318px;top:54px;width:532px;font-size:15.5px;line-height:21.5px;color:#eef0f4}
.bio p+p{margin-top:20px}
.portrait{position:absolute;border-radius:120px;padding:8px;border:2px solid var(--navy)}
.portrait__fill{width:100%;height:100%;border-radius:112px;background:linear-gradient(180deg,#e9ebee 0%,#d9dde2 45%,#2c3850 75%,#1e2840 100%)}
.profile--owen .portrait{left:620px;top:51px;width:228px;height:400px}
.profile--trevor .portrait{left:51px;top:56px;width:226px;height:410px;border-color:#e7e9ee}
.profile--trevor .portrait__fill{background:linear-gradient(180deg,#f2f3f5 0%,#e3e5e8 45%,#2b3550 75%,#1d2740 100%)}
.person{position:absolute;text-align:center}
.person__name{font-family:"EB Garamond",serif;font-weight:700;font-size:35px;line-height:40px;white-space:nowrap}
.person__role{font-size:16px;font-weight:300}
.profile--owen .person{left:600px;top:465px;width:268px}
.profile--trevor .person{left:24px;top:490px;width:280px}
.pill{position:absolute;display:flex;height:42px;border-radius:8px;overflow:hidden;border:2px solid var(--navy)}
.pill__phone{display:flex;align-items:center;gap:10px;padding:0 18px;background:#fff;color:var(--navy);font-family:"EB Garamond",serif;font-weight:700;font-size:20px;letter-spacing:1px;white-space:nowrap}
.pill__email{flex:1;display:flex;align-items:center;justify-content:center;gap:8px;background:var(--navy);color:#fff;font-family:"EB Garamond",serif;font-weight:700;font-size:14px;white-space:nowrap}
.pill svg{width:14px;height:14px;flex:none}
.profile--owen .pill{left:50px;top:476px;width:524px}
.profile--trevor .pill{left:318px;top:524px;width:532px;border-color:#fff}
.pill__email--light{background:#fff;color:var(--navy);border-left:2px solid var(--navy)}
.back-footer{position:absolute;left:0;top:1190px;width:900px;height:96px;display:flex;align-items:center;justify-content:space-between;padding:0 36px;font-size:13px;font-weight:300;color:var(--muted);white-space:nowrap}
.back-footer div{display:flex;align-items:center;gap:8px}
.back-footer svg{width:14px;height:14px}
.back-footer__name{font-family:"EB Garamond",serif;font-weight:700;font-size:20px;line-height:20px;color:var(--navy);text-align:center}
</style>
</head>
<body>

<section class="page page--front">
  <header class="brand-header">
    <span class="brand-dot"></span>
    <span class="brand-name">PINECREST</span>
  </header>

  <div class="hero-photo" role="img" aria-label="Aerial photograph of riverside homes and apartment towers along the river"></div>

  <div class="intro">
    <h1 class="intro__title">PINECREST ARE A NEW FACE IN THE DUNMORE &amp; KELVINHURST REAL ESTATE MARKET.</h1>
    <p class="intro__body">The Pinecrest team are both Dunmore ‘locals’ and are genuinely and sincerely committed to this community. They put people first and pursue exceptional outcomes for their clients.</p>
    <span class="intro__vision">This is the Founding Vision of Pinecrest</span>
  </div>

  <div class="reasons">
    <p class="reasons__item">If you’re thinking of selling</p>
    <p class="reasons__item">Interested in a free market appraisal</p>
    <p class="reasons__item">simply want to find out more about the Pinecrest team</p>
  </div>

  <div class="invite">
    <strong>Please reach out to Trevor or Owen for a chat.</strong> We’d love to shout you a coffee at The Marigold Coffee + Kitchen
  </div>

  <div class="front-contact">
    <div class="front-contact__name">Pinecrest<br>Real Estate</div>
    <div class="contact-lines">
      <div><svg viewBox="0 0 16 16"><rect x="1" y="3" width="14" height="10" rx="1" fill="#7d8699"/><path d="M1.5 3.5 8 9l6.5-5.5" stroke="#fff" stroke-width="1.2" fill="none"/></svg>hello@pinecrestrealestate-example.com.au</div>
      <div><svg viewBox="0 0 16 16" fill="none" stroke="#7d8699" stroke-width="1.3"><circle cx="8" cy="8" r="6.5"/><ellipse cx="8" cy="8" rx="3" ry="6.5"/><path d="M1.5 8h13"/></svg>www.pinecrestrealestate-example.com.au</div>
    </div>
  </div>

  <aside class="values">
    <h2 class="values__title">VALUES</h2>
    <div class="value" style="top:133px">
      <span class="value__icon"><svg viewBox="0 0 34 34" fill="none" stroke="#fff" stroke-width="2.6" stroke-linecap="round" stroke-linejoin="round"><path d="M8 18l6 6 12-13"/></svg></span>
      <span class="value__label">Integrity Always</span>
    </div>
    <div class="value" style="top:232px">
      <span class="value__icon"><svg viewBox="0 0 34 34" fill="#fff"><circle cx="17" cy="11" r="5"/><path d="M8 27c0-5 4-8 9-8s9 3 9 8z"/><circle cx="7" cy="14" r="3.5"/><circle cx="27" cy="14" r="3.5"/></svg></span>
      <span class="value__label">People First</span>
    </div>
    <div class="value" style="top:323px">
      <span class="value__icon"><svg viewBox="0 0 34 34" fill="none" stroke="#fff" stroke-width="2.4"><path d="M8 19v-3a9 9 0 0 1 18 0v3"/><rect x="6" y="18" width="5" height="8" rx="2" fill="#fff"/><rect x="23" y="18" width="5" height="8" rx="2" fill="#fff"/></svg></span>
      <span class="value__label">Outstanding<br>Customer Service</span>
    </div>
    <div class="value" style="top:422px">
      <span class="value__icon"><svg viewBox="0 0 34 34" fill="#fff"><path d="M6 14h5l12-7v20l-12-7H6z"/><rect x="9" y="20" width="4" height="7" rx="1"/></svg></span>
      <span class="value__label">Timely<br>Communication</span>
    </div>
    <div class="value" style="top:522px">
      <span class="value__icon"><svg viewBox="0 0 34 34" fill="#fff"><path d="M6 8h16a3 3 0 0 1 3 3v8a3 3 0 0 1-3 3H13l-5 4v-4H6a3 3 0 0 1-3-3v-8a3 3 0 0 1 3-3z"/><path d="M27 13h1a3 3 0 0 1 3 3v7a3 3 0 0 1-3 3v3l-4-3h-6v-2h5a3 3 0 0 0 3-3z"/></svg></span>
      <span class="value__label">Exceptional<br>Negotiation</span>
    </div>
  </aside>
</section>

<section class="page page--back">
  <article class="profile profile--owen">
    <div class="bio">
      <p>Owen has an in-depth understanding of all things property &amp; finance related. With a degree in property &amp; finance, diploma in finance &amp; mortgage broking, certificate IV in real estate practice, project management roles in residential property development, plus years of small business experience as co-founder/co-owner of The Marigold Coffee + Kitchen, his experience in managing competing demands and complex scenarios runs far and wide.</p>
      <p>Owen also has experience in corporate negotiations which is proving to be a very beneficial skill set. Owen is deeply committed to people and pursuing exceptional outcomes for his clients. He has built a reputation as a man of his word who is genuine and sincere and willing to go above and beyond for his clients.</p>
    </div>
    <div class="pill">
      <span class="pill__phone"><svg viewBox="0 0 16 16"><path d="M4 1.5l2.5 3-1.5 1.8a9 9 0 0 0 4.7 4.7l1.8-1.5 3 2.5-1.5 2.5C7 14.5 1.5 9 1.5 3z" fill="#1b2535"/></svg>0400 118 204</span>
      <span class="pill__email"><svg viewBox="0 0 16 16"><rect x="1" y="3" width="14" height="10" rx="1" fill="#fff"/><path d="M1.5 3.5 8 9l6.5-5.5" stroke="#1b2535" stroke-width="1.2" fill="none"/></svg>owen@pinecrestrealestate-example.com.au</span>
    </div>
    <div class="portrait"><div class="portrait__fill" role="img" aria-label="Headshot of Owen Pritchard in a navy suit"></div></div>
    <div class="person">
      <div class="person__name">Owen Pritchard</div>
      <div class="person__role">(Property Consultant)</div>
    </div>
  </article>

  <article class="profile profile--trevor">
    <div class="portrait"><div class="portrait__fill" role="img" aria-label="Headshot of Trevor Bungey in a navy suit and striped tie"></div></div>
    <div class="person">
      <div class="person__name">Trevor Bungey</div>
      <div class="person__role">(Director / Licensee)</div>
    </div>
    <div class="bio">
      <p>Trevor has worked in various roles inclusive of being a Real Estate Agent, Bank Manager, Financial Counsellor, Mortgage Broker, and previously a Commercial Pilot. He spent eight years in remote Western Australia, where he worked for an international mining company creating strategies to help support the well-being of employees. Trevor’s focus in life has always been to help people. To him, it is always about the relationship. Trevor gets enormous satisfaction from seeing individuals, families, and businesses thrive financially. He has become a skilled negotiator with extensive experience working for a number of corporations and private firms.</p>
      <p>What differentiates Trevor is his compassion and commitment to people. He works hard to be an excellent communicator with the aim of achieving great results. He has extensive sales experience with incredible ability to push the boundaries, think outside the box and meet or surpass expectations. This is why his clients keep coming back and continue to refer well into the future.</p>
    </div>
    <div class="pill">
      <span class="pill__phone"><svg viewBox="0 0 16 16"><path d="M4 1.5l2.5 3-1.5 1.8a9 9 0 0 0 4.7 4.7l1.8-1.5 3 2.5-1.5 2.5C7 14.5 1.5 9 1.5 3z" fill="#1b2535"/></svg>0400 362 917</span>
      <span class="pill__email pill__email--light"><svg viewBox="0 0 16 16"><rect x="1" y="3" width="14" height="10" rx="1" fill="#1b2535"/><path d="M1.5 3.5 8 9l6.5-5.5" stroke="#fff" stroke-width="1.2" fill="none"/></svg>trevor@pinecrestrealestate-example.com.au</span>
    </div>
  </article>

  <footer class="back-footer">
    <div><svg viewBox="0 0 16 16"><rect x="1" y="3" width="14" height="10" rx="1" fill="#7d8699"/><path d="M1.5 3.5 8 9l6.5-5.5" stroke="#fff" stroke-width="1.2" fill="none"/></svg>hello@pinecrestrealestate-example.com.au</div>
    <span class="back-footer__name">PINECREST<br>REAL ESTATE</span>
    <div><svg viewBox="0 0 16 16" fill="none" stroke="#7d8699" stroke-width="1.3"><circle cx="8" cy="8" r="6.5"/><ellipse cx="8" cy="8" rx="3" ry="6.5"/><path d="M1.5 8h13"/></svg>www.pinecrestrealestate-example.com.au</div>
  </footer>
</section>

</body>
</html>
```